Visitenkarten-Design für aufstrebendes, modernes und innovatives Elektrounternehmen
Zielgruppe
Unsere Firma ist im Bereich Elektro- und Gebäudetechnik angesiedelt.
Zielgruppe sind Privatkunden und Geschäftskunden.
Wir machen alles rund um das Thema Elektrotechnik, Elektroinstallation ....
Aufgabenstellung
Es soll ein ansprechendes modernes Design sein. Gerne auch mit Rückseite.
Wir sind ein junges aufstrebendes modernes und innovatives Unternehmen

```html
<!DOCTYPE html>
<html lang="de">
<head>
<meta charset="utf-8">
<title>Kerndl Visitenkarte</title>
<link rel="stylesheet" href="https://fonts.googleapis.com/css2?family=Arimo:wght@400;700&family=Ubuntu:wght@500&family=Open+Sans:wght@600&display=swap">
<style>
  :root {
    --stage: #4d4d4d;
    --mark: #2b2b2b;
    --paper: #f2f2f0;
    --teal: #1799ad;
    --olive: #c3b80d;
    --graphite: #5a5a5a;
    --muted: #7a7a7a;
    --ghost: #e3e3e1;
    --white: #f4f4f2;
  }
  * { margin: 0; padding: 0; box-sizing: border-box; }
  html, body { width: 1200px; height: 1200px; overflow: hidden; background: var(--stage); }
  .sheet { position: relative; width: 1200px; height: 1200px; }
  .crop { position: absolute; background: var(--mark); }
  .crop.v { width: 1px; height: 36px; }
  .crop.h { height: 1px; width: 35px; }
  .card {
    position: absolute; left: 399px; width: 409px; height: 263px;
    border-radius: 31px; overflow: hidden;
  }
  .card-front { top: 232px; background: var(--paper); }
  .card-back { top: 711px; background: var(--olive); }
  .card svg { position: absolute; inset: 0; }
  .t { position: absolute; white-space: nowrap; line-height: 1; }
  .brand {
    font-family: "Arimo", sans-serif; font-weight: 700; font-size: 58px;
    color: var(--graphite); letter-spacing: -1px;
  }
  .tagline {
    font-family: "Ubuntu", sans-serif; font-weight: 500; font-size: 12px;
    color: var(--teal); letter-spacing: 0.1px;
  }
  .person-name { font-family: "Arimo", sans-serif; font-size: 20px; color: var(--teal); letter-spacing: 0.6px; }
  .person-role { font-family: "Arimo", sans-serif; font-size: 11px; color: var(--muted); }
  .contact {
    position: absolute; right: 20px; top: 179px; text-align: right;
    font-family: "Arimo", sans-serif; font-size: 10px; line-height: 13.6px; color: var(--white);
  }
  .web {
    font-family: "Open Sans", sans-serif; font-weight: 600; font-size: 15px;
    color: var(--white); right: 25px; top: 234px;
  }
</style>
</head>
<body>
<div class="sheet">
  <!-- crop marks front -->
  <span class="crop v" style="left:399px;top:179px"></span>
  <span class="crop v" style="left:807px;top:179px"></span>
  <span class="crop v" style="left:399px;top:514px"></span>
  <span class="crop v" style="left:807px;top:514px"></span>
  <span class="crop h" style="left:346px;top:232px"></span>
  <span class="crop h" style="left:826px;top:232px"></span>
  <span class="crop h" style="left:346px;top:496px"></span>
  <span class="crop h" style="left:826px;top:496px"></span>
  <!-- crop marks back -->
  <span class="crop v" style="left:399px;top:657px"></span>
  <span class="crop v" style="left:807px;top:657px"></span>
  <span class="crop v" style="left:399px;top:992px"></span>
  <span class="crop v" style="left:807px;top:992px"></span>
  <span class="crop h" style="left:346px;top:711px"></span>
  <span class="crop h" style="left:826px;top:711px"></span>
  <span class="crop h" style="left:346px;top:974px"></span>
  <span class="crop h" style="left:826px;top:974px"></span>

  <section class="card card-front">
    <svg width="409" height="263" viewBox="0 0 409 263">
      <circle cx="109" cy="107" r="96" fill="none" stroke="var(--ghost)" stroke-width="8"/>
      <path d="M0 230 Q230 212 409 111 L409 263 L0 263 Z" fill="var(--teal)"/>
      <circle cx="56" cy="77" r="37" fill="var(--olive)"/>
    </svg>
    <span class="t brand" style="left:104px;top:45px">kerndl</span>
    <span class="t tagline" style="left:120px;top:99px">ELEKTRO- &amp; GEBÄUDETECHNIK</span>
    <span class="t person-name" style="left:26px;top:142px">Jonas Kerndl</span>
    <span class="t person-role" style="left:56px;top:167px">Managing Director</span>
    <div class="contact">
      Jonas Kerndl<br>
      Elektrotechnikermeister<br>
      Lindenweg 12 · 86150 Musterau<br>
      T 08231 480517<br>
      info@kerndl-licht-elektro.de
    </div>
  </section>

  <section class="card card-back">
    <svg width="409" height="263" viewBox="0 0 409 263">
      <circle cx="132" cy="131" r="108" fill="none" stroke="var(--white)" stroke-width="10"/>
    </svg>
    <span class="t brand" style="left:173px;top:89px">kerndl</span>
    <span class="t tagline" style="left:188px;top:142px">ELEKTRO- &amp; GEBÄUDETECHNIK</span>
    <span class="t web">www.kerndl-elektrotechnik.de</span>
  </section>
</div>
</body>
</html>
```